KW Holdings ltd*

I need a full website designed for for a 10,000m2 strorage facity which specialize in heavy commercial storage

it needs to be in english please

Target Market(s)

Comercial sector

Industry/Entity Type

Construction Company

Logo Text

KW

Coding

Coded - Design and coding required

Number of Pages Required

1 page

Font styles to use
Sans Serif

Colors
ec1f27
ffffff

Requirements
Must have
• Tel 0064 218846507
• email- liam@kwholdings.co.nz
Nice to have
• We specilize in large items with the facilty have 3 15tonne Gantry cranes and heavy mobile lifting equipment we can store items up to 20 tonne and we are fully covered and secure.
• square meter rates from 20m2 to 10,000 m2

```html
<!DOCTYPE html>
<html lang="en">
<head>
<meta charset="utf-8">
<title>KW Holdings ltd – Heavy Commercial Storage</title>
<link href="https://fonts.googleapis.com/css2?family=Montserrat:wght@400;500;600;700&family=Lato:wght@400;700&display=swap" rel="stylesheet">
<style>
:root{
  --red:#c0161d;
  --brand-red:#ec1f27;
  --white:#ffffff;
  --black:#000000;
  --card:rgba(20,22,26,0.88);
  --muted:#d9d9d9;
  --field:#ececec;
  --field-border:#b9b9b9;
  --label:#555555;
}
*{margin:0;padding:0;box-sizing:border-box}
html,body{width:1200px;height:2885px;overflow:hidden;background:var(--black)}
body{position:relative;font-family:'Montserrat',sans-serif;color:var(--white)}
.section{position:absolute;left:0;width:1200px;overflow:hidden}
.abs{position:absolute}

/* Header / hero */
.hero{top:0;height:614px}
.hero-photo{position:absolute;inset:0;background:
  radial-gradient(ellipse at 52% 60%,#6b6b66 0%,#3e3f3f 35%,#1f2021 70%,#141516 100%)}
.hero-shade{position:absolute;inset:0;background:rgba(0,0,0,0.35)}
.brand{position:absolute;left:248px;top:20px;width:110px;text-align:center}
.brand-mark{display:inline-block;width:44px;height:44px;border:3px solid var(--white);border-radius:50%}
.brand-name{display:block;margin-top:8px;font-weight:600;font-size:13px;letter-spacing:2px;color:var(--white)}
.nav{position:absolute;top:41px;left:466px;display:flex;gap:0;font-size:10.5px;font-weight:600;letter-spacing:.5px}
.nav a{color:var(--white);text-decoration:none;position:absolute;white-space:nowrap}
.btn-call{position:absolute;left:761px;top:32px;width:183px;height:32px;background:var(--red);color:var(--white);
  font-size:11px;font-weight:700;letter-spacing:1.6px;display:flex;align-items:center;justify-content:center}
.hero-title{position:absolute;top:232px;left:0;width:1200px;text-align:center;font-weight:700;font-size:68px;letter-spacing:-1px;line-height:1}
.hero-sub{position:absolute;top:312px;left:0;width:1200px;text-align:center;font-weight:700;font-size:26px;line-height:35px}
.btn-outline{position:absolute;border:2px solid var(--white);color:var(--white);display:flex;align-items:center;justify-content:center;
  font-weight:600;letter-spacing:2px}
.hero-cta{left:505px;top:412px;width:179px;height:42px;font-size:14px}
.scroll-arrow{position:absolute;left:587px;top:542px}

/* About */
.about{top:614px;height:615px}
.about-photo{position:absolute;inset:0;background:
  linear-gradient(180deg,#5d6b78 0%,#4a5662 25%,#46525a 45%,#5a4f4a 70%,#3b3433 100%)}
.about-shade{position:absolute;inset:0;background:rgba(0,0,0,0.38)}
.section-title{position:absolute;left:0;width:1200px;text-align:center;font-weight:500;font-size:31px}
.feature{position:absolute;width:158px;background:var(--card);text-align:center;padding:16px 14px 0}
.feature svg{display:block;margin:0 auto 8px}
.feature h3{font-size:13.5px;font-weight:700;line-height:15px;margin-bottom:6px;text-transform:uppercase}
.feature p{font-family:'Lato',sans-serif;font-size:11.5px;line-height:16px}
.about-text{position:absolute;left:626px;top:221px;width:300px;font-size:14.5px;line-height:21px;color:var(--white)}
.about-text p+p{margin-top:19px}
.btn-solid-white{position:absolute;left:626px;top:380px;width:206px;height:40px;background:var(--white);color:#111;
  font-size:14px;font-weight:600;letter-spacing:1.8px;display:flex;align-items:center;justify-content:center}

/* Services */
.services{top:1229px;height:732px;background:var(--black)}
.service-photo{position:absolute}
.photo-warehouse{left:267px;top:153px;width:320px;height:213px;background:
  linear-gradient(135deg,#1c3f6e 0%,#2c6eab 40%,#8fc3e6 60%,#2a5d8c 100%)}
.photo-container{left:612px;top:440px;width:319px;height:202px;background:
  linear-gradient(180deg,#e8eaec 0%,#c9ccd0 50%,#8a8f95 80%,#6d7176 100%)}
.service-title{position:absolute;font-size:13.5px;font-weight:700;letter-spacing:.5px}
.service-text{position:absolute;font-family:'Lato',sans-serif;font-size:12px;line-height:16px;font-weight:700;width:320px}
.quote-btn{height:40px;width:210px;font-size:14px}

/* Contact */
.contact{top:1961px;height:537px}
.contact-photo{position:absolute;inset:0;background:
  linear-gradient(180deg,#4f87b8 0%,#8cb3d2 30%,#c9d3da 50%,#a5a9a6 70%,#5d6a55 88%,#3c4a36 100%)}
.contact-shade{position:absolute;inset:0;background:rgba(0,0,0,0.4)}
.contact-form{position:absolute;left:406px;top:113px;width:386px;height:376px;background:var(--white);padding:16px 16px 0}
.field{margin-bottom:11px}
.field label{display:block;text-align:center;font-family:'Lato',sans-serif;font-size:7.5px;font-weight:700;color:var(--label);margin-bottom:3px}
.field label span{color:var(--red)}
.field .input{height:26px;background:var(--field);border:1px solid var(--field-border);font-family:'Lato',sans-serif;font-size:9px;color:#a0a0a0;padding:7px 6px}
.field .textarea{height:90px}
.btn-send{position:absolute;left:152px;top:311px;width:83px;height:29px;background:var(--red);color:var(--white);
  font-family:'Lato',sans-serif;font-weight:700;font-size:11px;display:flex;align-items:center;justify-content:center}

/* Footer */
.footer{top:2498px;height:387px;background:var(--black)}
.footer-brand{position:absolute;left:290px;top:57px;width:110px;text-align:center}
.footer-brand .brand-mark{border-color:var(--red)}
.footer-brand .brand-name{color:var(--red);font-size:14px}
.footer-company{position:absolute;left:297px;top:153px;font-size:12px;font-weight:700}
.rule{position:absolute;left:285px;width:690px;height:1px;background:var(--red)}
.footer-item{position:absolute;font-family:'Lato',sans-serif;font-size:10px;line-height:17px;color:var(--muted)}
.footer-icon{position:absolute}
</style>
</head>
<body>

<header class="section hero">
  <div class="hero-photo" role="img" aria-label="Photo of a tall warehouse racking aisle with a forklift"></div>
  <div class="hero-shade"></div>
  <div class="brand"><span class="brand-mark"></span><span class="brand-name">KW HOLDINGS</span></div>
  <nav class="nav">
    <a style="left:0">HOME</a>
    <a style="left:56px">ABOUT</a>
    <a style="left:118px">OUR SERVICES</a>
    <a style="left:219px">CONTACT</a>
  </nav>
  <div class="btn-call">CALL 0064 218846507</div>
  <h1 class="hero-title">10,000m2</h1>
  <p class="hero-sub">fully covered and secure<br>storage space</p>
  <div class="btn-outline hero-cta">GET IN TOUCH</div>
  <svg class="scroll-arrow" width="24" height="34" viewBox="0 0 24 34" fill="none" stroke="#fff" stroke-width="1.6">
    <line x1="12" y1="1" x2="12" y2="32"/><polyline points="2,22 12,32 22,22"/>
  </svg>
</header>

<section class="section about">
  <div class="about-photo" role="img" aria-label="Aerial photo of a container port with gantry cranes and the sea"></div>
  <div class="about-shade"></div>
  <h2 class="section-title" style="top:76px">About Us</h2>

  <div class="feature" style="left:262px;top:149px;height:149px">
    <svg width="20" height="20" viewBox="0 0 20 20" fill="none" stroke="#fff" stroke-width="2.2">
      <line x1="3" y1="3" x2="17" y2="17"/><line x1="17" y1="3" x2="3" y2="17"/>
      <polyline points="2,8 2,2 8,2"/><polyline points="12,2 18,2 18,8"/><polyline points="2,12 2,18 8,18"/><polyline points="18,12 18,18 12,18"/>
    </svg>
    <h3>Huge Space</h3>
    <p>10,000m2 (107,639sqf) with a flexible ratecard, from 20m2 to 10,000 m2.</p>
  </div>
  <div class="feature" style="left:434px;top:149px;height:149px">
    <svg width="22" height="20" viewBox="0 0 22 20" fill="none" stroke="#fff" stroke-width="1.8">
      <line x1="2" y1="4" x2="20" y2="4"/><line x1="9" y1="1" x2="9" y2="19"/><line x1="12" y1="1" x2="12" y2="19"/>
      <line x1="17" y1="4" x2="17" y2="10"/><rect x="15" y="10" width="4" height="3"/>
    </svg>
    <h3>3 Gantry<br>Cranes</h3>
    <p>Our three 15tonne gantry cranes are ready to serve you.</p>
  </div>
  <div class="feature" style="left:262px;top:315px;height:181px">
    <svg width="22" height="20" viewBox="0 0 22 20" fill="none" stroke="#fff" stroke-width="1.8">
      <rect x="2" y="10" width="14" height="6"/><line x1="4" y1="10" x2="4" y2="2"/><line x1="4" y1="2" x2="12" y2="2"/>
      <line x1="12" y1="2" x2="12" y2="7"/><circle cx="5" cy="18" r="1.5"/><circle cx="13" cy="18" r="1.5"/><line x1="16" y1="13" x2="21" y2="13"/>
    </svg>
    <h3>Mobile Lifting<br>Equipment</h3>
    <p>Our heavy mobile lifting equipment will make sure the loading and unloading process on time.</p>
  </div>
  <div class="feature" style="left:434px;top:315px;height:181px">
    <svg width="22" height="20" viewBox="0 0 22 20" fill="#fff">
      <path d="M2 8 L9 3 L16 8 V16 H2 Z"/><circle cx="16" cy="14" r="5" fill="#fff"/>
      <polyline points="13.5,14 15.5,16 18.5,12" fill="none" stroke="#14161a" stroke-width="1.6"/>
    </svg>
    <h3>Covered and<br>Secure</h3>
    <p>Our facility is modern, fully covered, and secure. We can securely store your items up to 20 tonne.</p>
  </div>

  <div class="about-text">
    <p>We specialize in large items with the facility, we have three 15tonne gantry cranes and heavy mobile lifting equipment.</p>
    <p>We can store items up to 20 tonne and we are fully covered and secure.</p>
  </div>
  <div class="btn-solid-white">CONTACT US NOW</div>
</section>

<section class="section services">
  <h2 class="section-title" style="top:75px">Our Services</h2>

  <div class="service-photo photo-warehouse" role="img" aria-label="Photo of a modern warehouse interior with roller doors"></div>
  <h3 class="service-title" style="left:612px;top:206px">WAREHOUSING</h3>
  <p class="service-text" style="left:612px;top:228px">Flexible ratecard, from 20m2 to 10,000 m2. Alarmed/direct link to police &amp; security, CCTV.</p>
  <div class="btn-outline quote-btn" style="left:612px;top:272px">REQUEST A QUOTE</div>

  <h3 class="service-title" style="right:613px;top:472px">VANNING/DEVANNING</h3>
  <p class="service-text" style="left:267px;top:494px;text-align:right">KW Holdings offer a professional vanning and de-vanning service for loading and unloading sea going containers 40’ 20’ plus high cube containers.</p>
  <div class="btn-outline quote-btn" style="left:376px;top:570px">REQUEST A QUOTE</div>
  <div class="service-photo photo-container" role="img" aria-label="Photo of a reach stacker lifting a shipping container onto a truck"></div>
</section>

<section class="section contact">
  <div class="contact-photo" role="img" aria-label="Photo of a large warehouse building under a cloudy sky"></div>
  <div class="contact-shade"></div>
  <h2 class="section-title" style="top:47px">Get in Touch</h2>
  <form class="contact-form">
    <div class="field"><label>First Name <span>*</span></label><div class="input">E.g. John</div></div>
    <div class="field" style="margin-top:22px"><label>Email Address <span>*</span></label><div class="input">E.g. john@doe.com</div></div>
    <div class="field" style="margin-top:22px"><label>Phone Number</label><div class="input">E.g. +64 210000000</div></div>
    <div class="field" style="margin-top:22px"><label>Message</label><div class="input textarea">Enter your message...</div></div>
    <div class="btn-send">SEND</div>
  </form>
</section>

<footer class="section footer">
  <div class="footer-brand"><span class="brand-mark"></span><span class="brand-name">KW HOLDINGS</span></div>
  <div class="footer-company">KW Holdings LTD</div>
  <div class="rule" style="top:184px"></div>

  <svg class="footer-icon" style="left:298px;top:198px" width="12" height="12" viewBox="0 0 12 12" fill="#fff"><path d="M12 0 L0 5 L5 7 L7 12 Z"/></svg>
  <div class="footer-item" style="left:297px;top:214px;width:170px">18 Harbour Quay, Wellington 6011, New Zealand</div>

  <svg class="footer-icon" style="left:528px;top:198px" width="12" height="12" viewBox="0 0 12 12" fill="#fff"><path d="M2 0 L4.5 0 L5.5 3 L4 4.5 C5 6.5 5.5 7 7.5 8 L9 6.5 L12 7.5 L12 10 C12 11 11 12 10 12 C5 12 0 7 0 2 C0 1 1 0 2 0 Z"/></svg>
  <div class="footer-item" style="left:528px;top:214px">0064218846507</div>

  <svg class="footer-icon" style="left:758px;top:199px" width="14" height="11" viewBox="0 0 14 11"><rect width="14" height="11" fill="#fff"/><polyline points="0,0 7,6 14,0" fill="none" stroke="#000" stroke-width="1.4"/></svg>
  <div class="footer-item" style="left:758px;top:214px">liam@kwholdings.co.nz</div>

  <div class="rule" style="top:279px"></div>
  <div class="footer-item" style="left:297px;top:290px">Opening Hours:</div>
  <div class="footer-item" style="left:528px;top:287px;line-height:20px">Monday-Thursday 7am-3.30pm<br>Friday 7am-3pm</div>
  <div class="footer-item" style="left:758px;top:290px;width:210px;line-height:19px">Special arrangements can be made for out of hours’ access.</div>
</footer>

</body>
</html>
```